Refresh of far from plain IT company website

Our web site is starting to show it's age. You can see the existing site here: www.plumbwick.net. As a growing company we want to come across as a dynamic collection of IT experts.

We want to update the design so are open to any colour palette and look, but want to retain our current table logo. We use the logo on our business cards but with a white background - see the attached file, so you don't need to keep the brown or the green.

The design should consider the range of browsers that will be looking at the site - so please show how it will look on a wide screen laptop and a 768x1024 tablet.

We want to add some pages about our team and their skills, probably with photos of each person on the team.

This is an uncoded project - the PSD files of the design is required, not coding.
Updates

Thanks everyone for the submissions so far.  It's a holiday day in the UK today but we will get some feedback on the designs so far out to you.

Target Market(s)

Architects and other creative types looking for IT support

Industry/Entity Type

Business

Font styles to use
Serif
Sans Serif

Requirements
Must have
• Must look good on a laptop and an iPad.

```html
<!DOCTYPE html>
<html lang="en">
<head>
<meta charset="utf-8">
<title>plumbwick — Serious IT Support for Business</title>
<link rel="stylesheet" href="https://fonts.googleapis.com/css2?family=Exo+2:ital,wght@1,600;1,700&family=Ubuntu:wght@300;400;500;700&display=swap">
<style>
:root{
  --plum:#9a0853;
  --plum-dark:#86064a;
  --gold:#d9ad00;
  --ink:#3a3a3a;
  --grey:#5b5b5b;
  --rule:#dcdcdc;
  --panel:#efefef;
}
*{box-sizing:border-box;margin:0;padding:0}
html,body{width:1026px;height:1200px;overflow:hidden}
body{position:relative;font-family:"Ubuntu",sans-serif;color:var(--ink);
  background:linear-gradient(#fff 0,#fff 122px,#e6e6e6 300px,#d8d8d8 450px,#fff 452px,#fff 100%)}
.abs{position:absolute}
.topbar{left:0;top:0;width:1026px;height:3px;background:var(--plum)}
.brand{left:195px;top:26px;display:flex;align-items:center;gap:14px}
.brand-mark{width:38px;height:38px;background:var(--gold)}
.brand-name{font-size:44px;font-weight:500;color:var(--plum);letter-spacing:-0.5px;line-height:1}
.call{right:190px;top:15px;font-size:15px;font-weight:300;color:var(--grey)}
.chat{left:726px;top:43px;width:110px;height:42px;border:1px solid #d0d0d0;border-radius:4px;background:#f4f4f4}
.chat-agent{position:absolute;left:3px;top:-8px;width:34px;height:48px;border-radius:17px 17px 4px 4px;background:linear-gradient(#6b4a3a,#e9d2c5)}
.chat-text{position:absolute;right:4px;top:6px;text-align:right;font-size:12px;font-weight:500;line-height:17px}
.chat-text b{color:var(--plum);font-weight:500;display:block}
.chat-text span{color:var(--gold)}
.nav{left:195px;top:97px;width:642px;height:25px;font-size:9.5px;font-weight:500;color:var(--grey);text-transform:uppercase}
.nav a{position:absolute;top:0;color:inherit;text-decoration:none}
.nav a.current{color:var(--plum)}
.nav .sep{position:absolute;top:0;width:1px;height:12px;background:#c4c4c4}
.nav-underline{left:195px;top:118px;width:37px;height:3px;background:var(--plum)}
.hero{left:195px;top:122px;width:642px;height:328px;
  background:radial-gradient(ellipse at 55% 45%,#4f8fb0 0,#1f5f86 40%,#0d3556 100%)}
.hero-title{left:212px;top:254px;font-family:"Exo 2",sans-serif;font-style:italic;font-weight:600;font-size:28px;line-height:29px;color:#fff;letter-spacing:-0.5px}
.dot{top:397px;width:10px;height:10px;border-radius:50%;background:#bfc7cc}
.dot.on{background:var(--plum);border:2px solid #fff}
.band{left:0;top:449px;width:1026px;height:4px;background:repeating-linear-gradient(135deg,var(--plum) 0 2px,#c36a97 2px 3px)}
.service{top:422px;width:120px;text-align:center;font-size:10px;font-weight:500;color:#2d2d2d}
.service .ico{width:52px;height:52px;margin:0 auto 10px;border-radius:50%;background:#555;border:3px solid #fff;box-shadow:0 1px 3px rgba(0,0,0,.35);display:flex;align-items:center;justify-content:center}
.service.active .ico{background:var(--plum);box-shadow:0 0 0 2px var(--gold)}
.h2{font-family:"Exo 2",sans-serif;font-style:italic;font-weight:700;font-size:17px;color:var(--plum);letter-spacing:-0.3px}
.rule{height:1px;background:var(--rule)}
.about-copy{left:195px;top:562px;width:413px;font-size:10.4px;line-height:18px;color:#333}
.about-copy p+p{margin-top:12px}
.more{left:540px;top:704px;font-size:10.5px;color:var(--gold)}
.team{left:636px;top:524px;width:192px;height:192px;border-radius:50%;border:3px solid var(--plum);padding:4px;background:#fff;box-shadow:0 6px 10px rgba(0,0,0,.15)}
.team-photo{width:100%;height:100%;border-radius:50%;overflow:hidden;position:relative;background:linear-gradient(#fff 0,#bcc8d9 45%,#6f7e95 65%)}
.team-label{position:absolute;left:0;bottom:0;width:100%;height:58px;background:var(--plum);color:#fff;font-size:20px;font-weight:500;text-align:center;padding-top:10px}
.box{top:786px;height:224px;background:var(--panel);border:3px solid #fff;outline:1px solid #d2d2d2;box-shadow:0 8px 8px -4px rgba(0,0,0,.25)}
.quote{position:absolute;left:0;width:100%;height:106px}
.avatar{position:absolute;left:18px;top:8px;width:62px;height:62px;border-radius:50%;border:3px solid #fff;box-shadow:0 1px 3px rgba(0,0,0,.3);background:linear-gradient(#e9e2da,#8b8f9c)}
.who{position:absolute;left:0;top:76px;width:124px;text-align:center;font-size:12px;font-weight:500;color:#333;line-height:13px}
.who small{display:block;font-size:8.5px;font-weight:300;color:#666;margin-top:2px}
.quote .vline{position:absolute;left:108px;top:8px;width:1px;height:90px;background:#dadada}
.qmark{position:absolute;font-family:Georgia,serif;font-size:22px;color:#999;line-height:1}
.qtext{position:absolute;left:124px;top:24px;width:170px;font-size:9.3px;line-height:12.7px;color:#333}
.news{position:absolute;left:22px;width:270px;height:74px}
.news .cal{position:absolute;left:0;top:2px}
.news .date{position:absolute;left:46px;top:0;font-size:9.5px;font-weight:500;color:var(--plum)}
.news .txt{position:absolute;left:46px;top:18px;font-size:9.5px;line-height:13.5px;color:#333}
.news-sep{position:absolute;left:22px;width:270px;height:1px;background:#dcdcdc}
.pager{top:1015px;display:flex;gap:6px}
.footer{left:0;top:1044px;width:1026px;height:126px;background:var(--plum-dark);color:#fff}
.f-h{position:absolute;top:18px;font-size:13px;font-weight:400}
.links{position:absolute;top:44px;font-size:8.5px;line-height:18px;text-transform:uppercase}
.links li{list-style:none;padding-left:12px;position:relative}
.links li::before{content:"›";position:absolute;left:0;color:var(--gold);font-size:11px;line-height:16px}
.f-sep{position:absolute;top:42px;width:1px;height:70px;background:rgba(255,255,255,.25)}
.news-copy{position:absolute;left:426px;top:48px;width:150px;font-size:9px;line-height:11px}
.email{position:absolute;left:425px;top:67px;width:114px;height:16px;background:#fff;border-radius:2px;font-size:8px;color:#999;padding:3px 5px}
.submit{position:absolute;left:425px;top:90px;width:53px;height:17px;border:1px solid var(--gold);border-radius:3px;font-size:9.5px;font-weight:700;text-align:center;line-height:15px}
.map{position:absolute;left:630px;top:47px;width:81px;height:62px;background:linear-gradient(135deg,#d9dcd3,#b9c2b4);border:1px solid #fff}
.contact{position:absolute;left:722px;font-size:8.8px;line-height:11px;display:flex;gap:6px}
.contact svg{flex:none}
.bottom{left:0;top:1170px;width:1026px;height:30px;background:var(--gold);color:#fff}
.copy{position:absolute;left:195px;top:8px;font-size:10.5px;font-weight:300}
.social{position:absolute;top:4px;width:22px;height:22px;border-radius:50%;background:#fff;box-shadow:0 0 0 1px rgba(0,0,0,.1)}
.social.first{background:#2f9bd4;border:2px solid #fff}
</style>
</head>
<body>
<div class="abs topbar"></div>

<header>
  <div class="abs brand"><span class="brand-mark"></span><span class="brand-name">plumbwick</span></div>
  <div class="abs call">CALL US: 020 7946 0182</div>
  <div class="abs chat">
    <div class="chat-agent" role="img" aria-label="Support agent with headset"></div>
    <div class="chat-text"><b>LIVE CHATT</b><span>AVAILABLE</span></div>
  </div>
  <nav class="abs nav">
    <a class="current" style="left:3px">Home</a><span class="sep" style="left:51px"></span>
    <a style="left:70px">About Us</a><span class="sep" style="left:134px"></span>
    <a style="left:152px">What We Do</a><span class="sep" style="left:232px"></span>
    <a style="left:251px">News Blog</a><span class="sep" style="left:323px"></span>
    <a style="left:343px">Articles</a><span class="sep" style="left:403px"></span>
    <a style="left:423px">Clients</a><span class="sep" style="left:478px"></span>
    <a style="left:497px">Partners</a><span class="sep" style="left:563px"></span>
    <a style="left:582px">Contact Us</a>
  </nav>
  <div class="abs nav-underline"></div>
</header>

<section>
  <div class="abs hero" role="img" aria-label="Businessman in a suit working on holographic screens over a world map"></div>
  <h1 class="abs hero-title">SERIOUS IT SUPPORT<br>FOR BUSINESS</h1>
  <span class="abs dot on" style="left:481px"></span>
  <span class="abs dot" style="left:500px"></span>
  <span class="abs dot" style="left:518px"></span>
  <span class="abs dot" style="left:537px"></span>
</section>

<div class="abs band"></div>

<section>
  <div class="abs service" style="left:196px">
    <div class="ico"><svg width="26" height="26" viewBox="0 0 26 26"><path d="M5 21 L15 11 M15 11a5 5 0 1 0 3-6l-3 3 1 2 2 1 3-3a5 5 0 0 1-6 3" stroke="#fff" stroke-width="3" fill="none" stroke-linecap="round"/></svg></div>It Support &amp; Management</div>
  <div class="abs service" style="left:327px">
    <div class="ico"><svg width="30" height="22" viewBox="0 0 30 22"><path d="M8 19h15a5 5 0 0 0 0-10 7 7 0 0 0-13-2 6 6 0 0 0-2 12z" stroke="#fff" stroke-width="2.5" fill="none"/></svg></div>Cloud Computing</div>
  <div class="abs service active" style="left:455px">
    <div class="ico"><svg width="20" height="28" viewBox="0 0 20 28"><rect x="5" y="11" width="10" height="15" fill="#fff"/><path d="M10 2c3 4 6 5 4 9H6c-2-4 2-5 4-9z" fill="#fff"/></svg></div>Disaster Recovery</div>
  <div class="abs service" style="left:586px">
    <div class="ico"><svg width="20" height="28" viewBox="0 0 20 28"><rect x="5" y="3" width="10" height="16" fill="#fff"/><path d="M10 19v5M3 25h14" stroke="#fff" stroke-width="2"/></svg></div>Virtualisation</div>
  <div class="abs service" style="left:709px">
    <div class="ico"><svg width="28" height="26" viewBox="0 0 28 26"><path d="M14 3 3 23h22z" stroke="#fff" stroke-width="2.5" fill="none"/><path d="M8 17h12M14 3v20" stroke="#fff" stroke-width="2"/></svg></div>CAD Services</div>
</section>

<section>
  <h2 class="abs h2" style="left:197px;top:529px">ABOUT US</h2>
  <div class="abs rule" style="left:195px;top:552px;width:413px"></div>
  <div class="abs about-copy">
    <p>Lorem ipsum dolor sit amet, consectetuer adipiscing elit, sed diam nonummy nibh euismod tincidunt ut laoreet dolore magna aliquam erat volutpat. Ut wisi enim ad minim veniam, quis nostrud exerci tation ullamcorper suscipit lobortis nisl ut aliquip ex ea comsed diam nonummy nibh euismod tincidunt ut laoreet dolore magna aliquam erat volutpat.</p>
    <p>Lorem ipsum dolor sit amet, consectetuer adipiscing elit, sed diam nonummy nibh euismod tincidunt ut laoreet dolore magna aliquam erat volutpat. Ut wisi enim ad minim veniam, quis nostrud....</p>
  </div>
  <a class="abs more">READ MORE...</a>
  <div class="abs team">
    <div class="team-photo" role="img" aria-label="Group photo of the team in business shirts">
      <div class="team-label">OUR TEAM</div>
    </div>
  </div>
</section>

<section>
  <h2 class="abs h2" style="left:198px;top:751px">TESTIMONIALS</h2>
  <div class="abs rule" style="left:196px;top:776px;width:307px"></div>
  <div class="abs box" style="left:196px;width:307px">
    <div class="quote" style="top:6px">
      <div class="avatar" role="img" aria-label="Portrait of a client"></div>
      <div class="who">Alan Pembrey<small>Businessman</small></div>
      <span class="qmark" style="left:108px;top:10px">“</span>
      <div class="qtext" style="top:22px">Lorem ipsum dolor sit amet, consectetuer adipiscing elit, sed diam nonummyol nibh euismod<br>tincidunt ut laoreet dolore magnarpl aliquam erat volutpat. Ut wisi enim adm minim.</div>
      <span class="qmark" style="left:250px;top:86px">”</span>
    </div>
    <div class="quote" style="top:115px">
      <div class="avatar" role="img" aria-label="Portrait of a client"></div>
      <div class="who">Alan Pembrey<small>Businessman</small></div>
      <span class="qmark" style="left:108px;top:10px">“</span>
      <div class="qtext" style="top:22px">Lorem ipsum dolor sit amet, consectetuer adipiscing elit, sed diam nonummyol nibh euismod<br>tincidunt ut laoreet dolore magnarpl aliquam erat volutpat. Ut wisi enim adm minim.</div>
      <span class="qmark" style="left:244px;top:88px">”</span>
    </div>
  </div>
  <div class="abs pager" style="left:325px">
    <svg width="14" height="14" viewBox="0 0 14 14"><circle cx="7" cy="7" r="6" fill="none" stroke="#555"/><path d="M10 7H4M6 5 4 7l2 2" stroke="#555" fill="none"/></svg>
    <svg width="14" height="14" viewBox="0 0 14 14"><circle cx="7" cy="7" r="6" fill="none" stroke="#555"/><path d="M4 7h6M8 5l2 2-2 2" stroke="#555" fill="none"/></svg>
  </div>

  <h2 class="abs h2" style="left:530px;top:752px">LATEST NEWS</h2>
  <div class="abs rule" style="left:530px;top:776px;width:308px"></div>
  <div class="abs box" style="left:530px;width:308px">
    <div class="news" style="top:20px">
      <svg class="cal" width="30" height="30" viewBox="0 0 30 30"><rect x="1" y="4" width="28" height="25" rx="2" fill="none" stroke="#555" stroke-width="2"/><path d="M1 10h28M8 1v6M22 1v6" stroke="#555" stroke-width="2"/><g fill="#555"><rect x="5" y="13" width="4" height="3"/><rect x="11" y="13" width="4" height="3"/><rect x="17" y="13" width="4" height="3"/><rect x="23" y="13" width="3" height="3"/><rect x="5" y="18" width="4" height="3"/><rect x="11" y="18" width="4" height="3"/><rect x="17" y="18" width="4" height="3"/><rect x="23" y="18" width="3" height="3"/><rect x="5" y="23" width="4" height="3"/><rect x="11" y="23" width="4" height="3"/><rect x="17" y="23" width="4" height="3"/></g></svg>
      <div class="date">12-APR-2014</div>
      <div class="txt">Lorem ipsum dolor sit amet, consectetuer<br>adipiscil ng elit, sed diam nonummy nibh...</div>
    </div>
    <div class="news-sep" style="top:73px"></div>
    <div class="news" style="top:94px">
      <svg class="cal" width="30" height="30" viewBox="0 0 30 30"><rect x="1" y="4" width="28" height="25" rx="2" fill="none" stroke="#555" stroke-width="2"/><path d="M1 10h28M8 1v6M22 1v6" stroke="#555" stroke-width="2"/><g fill="#555"><rect x="5" y="13" width="4" height="3"/><rect x="11" y="13" width="4" height="3"/><rect x="17" y="13" width="4" height="3"/><rect x="23" y="13" width="3" height="3"/><rect x="5" y="18" width="4" height="3"/><rect x="11" y="18" width="4" height="3"/><rect x="17" y="18" width="4" height="3"/><rect x="23" y="18" width="3" height="3"/><rect x="5" y="23" width="4" height="3"/><rect x="11" y="23" width="4" height="3"/><rect x="17" y="23" width="4" height="3"/></g></svg>
      <div class="date">15-APR-2014</div>
      <div class="txt">Lorem ipsum dolor sit amet, consectetuer<br>adipiscil ng elit, sed diam nonummy nibh...</div>
    </div>
    <div class="news-sep" style="top:147px"></div>
    <div class="news" style="top:168px">
      <svg class="cal" width="30" height="30" viewBox="0 0 30 30"><rect x="1" y="4" width="28" height="25" rx="2" fill="none" stroke="#555" stroke-width="2"/><path d="M1 10h28M8 1v6M22 1v6" stroke="#555" stroke-width="2"/><g fill="#555"><rect x="5" y="13" width="4" height="3"/><rect x="11" y="13" width="4" height="3"/><rect x="17" y="13" width="4" height="3"/><rect x="23" y="13" width="3" height="3"/><rect x="5" y="18" width="4" height="3"/><rect x="11" y="18" width="4" height="3"/><rect x="17" y="18" width="4" height="3"/><rect x="23" y="18" width="3" height="3"/><rect x="5" y="23" width="4" height="3"/><rect x="11" y="23" width="4" height="3"/><rect x="17" y="23" width="4" height="3"/></g></svg>
      <div class="date">17-APR-2014</div>
      <div class="txt">Lorem ipsum dolor sit amet, consectetuer<br>adipiscil ng elit, sed diam nonummy nibh...</div>
    </div>
  </div>
  <div class="abs pager" style="left:666px">
    <svg width="14" height="14" viewBox="0 0 14 14"><circle cx="7" cy="7" r="6" fill="none" stroke="#555"/><path d="M10 7H4M6 5 4 7l2 2" stroke="#555" fill="none"/></svg>
    <svg width="14" height="14" viewBox="0 0 14 14"><circle cx="7" cy="7" r="6" fill="none" stroke="#555"/><path d="M4 7h6M8 5l2 2-2 2" stroke="#555" fill="none"/></svg>
  </div>
</section>

<footer class="abs footer">
  <div class="f-h" style="left:196px">Quick Links</div>
  <ul class="links" style="left:196px"><li>Home</li><li>About Us</li><li>What We Do</li><li>News Blog</li></ul>
  <ul class="links" style="left:280px"><li>Articles</li><li>Clients</li><li>Partners</li><li>Contact Us</li></ul>
  <span class="f-sep" style="left:385px"></span>
  <div class="f-h" style="left:426px">Newsletter Signup</div>
  <div class="news-copy">Lorem ipsum dolor sit amet, consectetuer adipiscing elit.</div>
  <div class="email">Enter your email address</div>
  <div class="submit">SUBMIT</div>
  <span class="f-sep" style="left:589px"></span>
  <div class="f-h" style="left:630px">Contact Info</div>
  <div class="map" role="img" aria-label="Street map showing office location"></div>
  <div class="contact" style="top:48px"><svg width="9" height="12" viewBox="0 0 9 12"><path d="M4.5 12S0 6.5 0 4.5a4.5 4.5 0 0 1 9 0C9 6.5 4.5 12 4.5 12z" fill="#d9ad00"/><circle cx="4.5" cy="4.5" r="1.6" fill="#86064a"/></svg><span>Lorem ipsum dolor sit<br>amet, consectetuer<br>adipiscing elit.</span></div>
  <div class="contact" style="top:90px"><svg width="9" height="9" viewBox="0 0 9 9"><circle cx="4.5" cy="4.5" r="4" fill="none" stroke="#d9ad00"/><path d="M3 2.5l1 1.5-.6.6 1.5 1.5.6-.6 1.5 1" stroke="#d9ad00" fill="none"/></svg><span>020 7946 0182</span></div>
  <div class="contact" style="top:106px"><svg width="10" height="8" viewBox="0 0 10 8"><rect width="10" height="8" fill="#d9ad00"/><path d="M0 0l5 4 5-4" stroke="#86064a" fill="none"/></svg><span>website@plumbwick.net</span></div>
</footer>

<div class="abs bottom">
  <div class="copy">© 2014 plumbwick. All Rights Reserved.</div>
  <span class="social first" style="left:735px"></span>
  <span class="social" style="left:761px"></span>
  <span class="social" style="left:788px"></span>
  <span class="social" style="left:815px"></span>
</div>
</body>
</html>
```